The Linen Loft Co

We need a business card design for our wardrobe company.
Please visit our website www.gentlelinenlofts.com to get an idea of who we are.

```html
<!DOCTYPE html>
<html lang="en">
<head>
<meta charset="utf-8">
<title>The Linen Loft Co — Business Card</title>
<link rel="stylesheet" href="https://fonts.googleapis.com/css2?family=Jost:wght@400&family=Roboto:wght@400;500;700&display=swap">
<style>
  :root {
    --backdrop: #e4e2de;
    --card-white: #f7f7f5;
    --card-dark-top: #8c8b88;
    --card-dark-mid: #3a3937;
    --card-dark-bottom: #161616;
    --copper: #c48a5a;
    --cream: #f1e6cf;
    --divider: #cfb895;
  }
  * { margin: 0; padding: 0; box-sizing: border-box; }
  html, body {
    width: 1200px;
    height: 900px;
    overflow: hidden;
    background: var(--backdrop);
  }
  .canvas {
    width: 1200px;
    height: 900px;
    display: flex;
    flex-direction: column;
    align-items: center;
    justify-content: center;
    gap: 60px;
  }
  .card {
    width: 630px;
    height: 360px;
    position: relative;
    box-shadow: 0 6px 18px rgba(0, 0, 0, 0.18);
  }

  /* Back side */
  .card--back {
    background: var(--card-white);
    display: flex;
    align-items: center;
    justify-content: center;
  }
  .contact {
    font-family: "Jost", "Futura", sans-serif;
    color: var(--copper);
    font-size: 21px;
    line-height: 1.22;
    text-align: center;
  }
  .contact__address { margin-bottom: 20px; }

  /* Front side */
  .card--front {
    background: linear-gradient(160deg, var(--card-dark-top) 0%, var(--card-dark-mid) 40%, var(--card-dark-bottom) 100%);
    display: flex;
    align-items: center;
    padding: 0 40px 0 48px;
  }
  .brand {
    display: flex;
    align-items: center;
    gap: 18px;
    margin-top: 70px;
  }
  .brand__mark {
    width: 26px;
    height: 26px;
    background: var(--copper);
    flex: none;
  }
  .brand__text {
    font-family: "Roboto", sans-serif;
    color: var(--copper);
  }
  .brand__name {
    font-size: 19px;
    font-weight: 500;
    letter-spacing: 0.3px;
  }
  .brand__tagline {
    font-size: 17px;
    font-weight: 500;
    margin-top: 4px;
    padding-left: 30px;
  }
  .divider {
    width: 1px;
    height: 110px;
    background: var(--divider);
    margin: 0 26px;
    flex: none;
  }
  .person {
    font-family: "Roboto", sans-serif;
    color: var(--cream);
    margin-bottom: 20px;
  }
  .person__name {
    font-size: 29px;
    font-weight: 700;
    line-height: 1.05;
  }
  .person__role {
    font-size: 19px;
    font-weight: 500;
    margin-top: 2px;
  }
</style>
</head>
<body>
  <main class="canvas">
    <section class="card card--back" aria-label="Card back">
      <div class="contact">
        <p class="contact__address">Marlow House, 42 Ferris Lane<br>London N4 7QT</p>
        <p class="contact__phone">020 7946 0815</p>
        <p class="contact__email">info@gentlelinenlofts.com</p>
        <p class="contact__web">www.gentlelinenlofts.com</p>
      </div>
    </section>

    <section class="card card--front" aria-label="Card front">
      <div class="brand">
        <span class="brand__mark" aria-hidden="true"></span>
        <div class="brand__text">
          <p class="brand__name">THE LINEN LOFT CO</p>
          <p class="brand__tagline">Stored with Quiet Care</p>
        </div>
      </div>
      <span class="divider" aria-hidden="true"></span>
      <div class="person">
        <p class="person__name">Daniel Hart</p>
        <p class="person__role">President</p>
      </div>
    </section>
  </main>
</body>
</html>
```